New Bicycle shop business card

Hi!
I'm looking for a business card for my new proffesional bike mechanics shop. This shop is only for fixing broken bikes and not selling bikes.
Peferbly a modern and sleek and modern design.
Colors: black, grey, red, white
Information:
Name: Rijwielwerkplaats Vanhoutte
Shop owner: Bart Vanhoutte & Marieke Segers
Website: www.rijwielwerkplaats-vanhoutte.be
Email: info@rijwielwerkplaats-vanhoutte.be
Phone number: +32471902368
Street adres: Kerkweg 46
9940 Bellebeke
Slogan/shop information: Herstellingen van alle merken.
Logo: see files.
Target Market(s)
People who seek a mechanic to fix or upgrade their bikes.
Contact Information for Business Card
Information:
Website: info@rijwielwerkplaats-vanhoutte.be
9940 Bellebeke
Logo: see files.

```html
<!DOCTYPE html>
<html lang="nl">
<head>
<meta charset="utf-8">
<title>Rijwielwerkplaats Vanhoutte – visitekaartje</title>
<link href="https://fonts.googleapis.com/css2?family=Lato:wght@400;700;900&display=swap" rel="stylesheet">
<style>
  :root {
    --red: #e2163f;
    --red-soft: #e9395c;
    --black: #1d1413;
    --grey: #9a9a9a;
    --paper: #fcf8f8;
    --backdrop: #d9d9d9;
    --ink: #1e1e1e;
  }
  * { box-sizing: border-box; margin: 0; padding: 0; }
  html, body {
    width: 1200px; height: 782px; overflow: hidden;
    background: var(--backdrop);
    font-family: "Lato", sans-serif;
  }
  .stage {
    width: 1200px; height: 782px;
    display: flex; align-items: center; justify-content: center; gap: 40px;
  }
  .card {
    position: relative;
    width: 540px; height: 309px;
    overflow: hidden;
    box-shadow: 0 6px 18px rgba(0,0,0,.25);
  }

  /* Front */
  .card-front { background: var(--paper); }
  .brand {
    position: absolute; left: 30px; top: 110px; width: 215px;
    display: flex; align-items: center; gap: 10px;
  }
  .brand-mark { flex: none; width: 16px; height: 16px; background: var(--red); }
  .brand-name {
    font-weight: 900; font-size: 19px; line-height: 1.15;
    color: var(--black); text-transform: uppercase; letter-spacing: .5px;
  }
  .divider {
    position: absolute; left: 258px; top: 92px;
    width: 1px; height: 110px; background: var(--grey);
  }
  .contact {
    position: absolute; left: 272px; top: 88px; right: 14px;
    color: var(--ink); font-size: 13px; line-height: 1.45;
  }
  .contact-names {
    color: var(--red); font-weight: 700; font-size: 13px;
    text-transform: uppercase; letter-spacing: .2px;
  }
  .contact-role { font-size: 12.5px; margin-bottom: 2px; }
  .contact-line { display: flex; align-items: center; gap: 6px; }
  .contact-line svg { flex: none; width: 10px; height: 10px; fill: var(--red); }
  .contact-address { margin-top: 2px; }
  .bands { position: absolute; left: 0; bottom: 0; width: 540px; height: 90px; }

  /* Back */
  .card-back { background: var(--red); }
  .back-pattern {
    position: absolute; inset: 0;
    background: linear-gradient(135deg, var(--red) 0%, var(--red-soft) 50%, var(--red) 100%);
  }
  .back-brand {
    position: absolute; left: 300px; top: 120px;
    display: flex; align-items: center; gap: 8px;
  }
  .back-brand-mark { width: 12px; height: 12px; border-radius: 50%; background: #fff; }
  .back-brand-name { color: #fff; font-weight: 900; font-size: 13px; text-transform: uppercase; letter-spacing: .5px; }
  .slogan {
    position: absolute; left: 150px; top: 196px;
    color: #fff; font-size: 14px; letter-spacing: .3px; text-transform: uppercase;
  }
</style>
</head>
<body>
<main class="stage">
  <section class="card card-front">
    <div class="brand">
      <span class="brand-mark"></span>
      <span class="brand-name">Rijwielwerkplaats Vanhoutte</span>
    </div>
    <div class="divider"></div>
    <div class="contact">
      <p class="contact-names">Bart Vanhoutte &amp; Marieke Segers</p>
      <p class="contact-role">Owner</p>
      <p class="contact-line">
        <svg viewBox="0 0 10 10"><path d="M2 0.5 L3.6 2.8 L2.8 3.8 Q4 6.2 6.2 7.2 L7.2 6.4 L9.5 8 L8.4 9.5 Q1 8.5 0.5 1.6 Z"/></svg>
        +32471902368
      </p>
      <p class="contact-line">
        <svg viewBox="0 0 10 10"><path d="M0 1.5 H10 V8.5 H0 Z M0.8 2.2 L5 5.4 L9.2 2.2 Z" fill-rule="evenodd"/></svg>
        info@rijwielwerkplaats-vanhoutte.be
      </p>
      <p class="contact-line">
        <svg viewBox="0 0 10 10"><circle cx="5" cy="5" r="4.6"/></svg>
        www.rijwielwerkplaats-vanhoutte.be
      </p>
      <p class="contact-address">Kerkweg 46<br>9940 Bellebeke</p>
    </div>
    <svg class="bands" viewBox="0 0 540 90" preserveAspectRatio="none">
      <polygon points="0,0 240,62 240,90 0,90" fill="var(--black)"/>
      <polygon points="240,62 540,80 540,90 240,90" fill="var(--red)"/>
      <line x1="240" y1="62" x2="540" y2="80" stroke="var(--paper)" stroke-width="0"/>
    </svg>
  </section>

  <section class="card card-back">
    <div class="back-pattern" role="img" aria-label="Herhalend patroon van het bedrijfsembleem in lichtrood op rood"></div>
    <div class="back-brand">
      <span class="back-brand-mark"></span>
      <span class="back-brand-name">Rijwielwerkplaats Vanhoutte</span>
    </div>
    <p class="slogan">Herstellingen van alle merken</p>
  </section>
</main>
</body>
</html>
```